Top header for website

Header for website Size is 1000px x 120px
I have CS5 so will need the source files photoshop, illustrator etc, so I can change text and photos.
Photos attached, includes example header and screenshot of eg site
Brief:
I need a website header for golfers where I can change the photos and their name.
The header needs to have these things.
- pictures of the golfer (use from pics attached)
- Their name
- Also under there name is smaller text I need a line of text you can just say "Offical Website" in your e.g to me
so for example you should have
Colin Perrault
Offical Website
And some photos that are blended with some nice golf background or some grass or other ideas that you come up with that will look better than mine I'm sure :)
Size is 1000px x 120px
It needs to look professional and blend in nicely. I don't mind how many photos are used maybe 1-4?
The text needs to look professional too but not boring.
The header you create will be used on a website for a Professional Golfer (tour pro) their job is golf, their website needs to showcase them and promote them as best as possible.
As I said above I will need to swap photos easily and edit the text so will need the source files.
So a important point here. I guess there is no need to blend or do anything to the photos you add as I will actually need to change the photos and just need a simple template that I can swap photos and edit their name.
Ultimately I would like 3 versions of the header done and source files for all 3 so I can give them(the golfers) a choice of header type.
See how you go.
Remember that the header must have the ability for me to easily swap images and of course change the text.
My goal is to use the same header for each golfer but obviously with their images and their name.
I have CS5 so will need the source files photoshop, illustrator etc
2 example headers are attached to show you my attempts :) Please do something better.
I don't want any flash.

```html
<!DOCTYPE html>
<html lang="en">
<head>
<meta charset="utf-8">
<title>Colin Perrault – Official Website Header</title>
<link rel="stylesheet" href="https://fonts.googleapis.com/css2?family=Open+Sans:ital,wght@0,700;1,400&display=swap">
<style>
  :root {
    --sky: #e7ecd9;
    --haze: #b7c98f;
    --grass-light: #7fb23a;
    --grass: #4f8a1f;
    --grass-dark: #2c5512;
    --portrait-bg: #6f7f4a;
    --portrait-mid: #c9c3b2;
    --frame: #ffffff;
    --name: #ffffff;
    --tagline: #f2ee1b;
    --shadow: rgba(0, 0, 0, 0.75);
  }
  html, body {
    margin: 0;
    padding: 0;
    width: 1200px;
    height: 144px;
    overflow: hidden;
    background: #ffffff;
  }
  .site-header {
    position: relative;
    width: 1200px;
    height: 144px;
    overflow: hidden;
  }
  .hero-scene {
    position: absolute;
    inset: 0;
    background:
      radial-gradient(ellipse 260px 90px at 170px 80px, rgba(255,255,255,0.55), transparent 70%),
      radial-gradient(ellipse 200px 70px at 380px 60px, rgba(60,70,80,0.45), transparent 70%),
      linear-gradient(180deg, var(--sky) 0%, var(--haze) 22%, var(--grass-light) 42%, var(--grass) 68%, var(--grass-dark) 100%);
  }
  .hero-scene::after {
    content: "";
    position: absolute;
    inset: 0;
    background: linear-gradient(90deg, transparent 55%, rgba(20, 45, 10, 0.45) 100%);
  }
  .golfer-portrait {
    position: absolute;
    left: 600px;
    top: 8px;
    width: 162px;
    height: 124px;
    border: 3px solid var(--frame);
    background:
      radial-gradient(ellipse 60px 70px at 95px 85px, var(--portrait-mid), transparent 75%),
      linear-gradient(160deg, var(--portrait-bg), #4e5c33);
  }
  .golfer-identity {
    position: absolute;
    right: 38px;
    top: 28px;
    text-align: right;
    font-family: "Open Sans", Arial, sans-serif;
  }
  .golfer-name {
    margin: 0;
    font-weight: 700;
    font-size: 46px;
    line-height: 1.1;
    color: var(--name);
    text-shadow: 2px 2px 4px var(--shadow);
    letter-spacing: -0.5px;
  }
  .golfer-tagline {
    margin: 0;
    font-style: italic;
    font-weight: 400;
    font-size: 30px;
    line-height: 1.2;
    color: var(--tagline);
    text-shadow: 1px 1px 3px var(--shadow);
  }
</style>
</head>
<body>
  <header class="site-header">
    <div class="hero-scene" role="img" aria-label="Golf ball on a tee and a fairway wood resting on green grass, trees in the distance"></div>
    <div class="golfer-portrait" role="img" aria-label="Photo of the golfer in a white shirt and cap"></div>
    <div class="golfer-identity">
      <h1 class="golfer-name">Colin Perrault</h1>
      <p class="golfer-tagline">Offical Website</p>
    </div>
  </header>
</body>
</html>
```